New Business Card Design Project

I need a design for business cards, i am an electrical business called "Corvane Electrical and Communications" i need the cards to be double sided with the company logo on the back (attached) the front needs to say my company name, web site, email address, telephone number, and ABN number and electrical license number. I am open to different arrangements of the information but would like the background to be incorporating something electrical or something that looks smart. open to all additional ideas also.

The company colours are orange and grey see logo attached.

Business Name: Corvane Electrical and Communications
Website: corvaneelectricalandcomms.example.com.au
Email: brent@corvaneelectricalandcomms.example.com.au
Telephone(mobile): 0481209736
ABN: 71208349162
Lic No: 418273D

Target Market(s)

Business entities, Project Managers, Accounts, Clients

Industry/Entity Type

Electrician

Contact Information for Business Card

I need a design for business cards, i am an electrical business called "Corvane Electrical and Communications" i need the cards to be double sided with the company logo on the back (attached) the front needs to say my company name

Font styles to use
Serif
Sans Serif

Colors
f37122
5c5c5c

Requirements
Must have
• Must have the Logo on the back open to different ways of it being on the back but had in mind to keep it central but again open to other options
Nice to have
• A real modern cool background that is eye catching yet contemporary
Should not have
• No backgrounds of a light bulb or plug or anything like that

```html
<!DOCTYPE html>
<html lang="en">
<head>
<meta charset="utf-8">
<title>Corvane Electrical and Communications – Business Cards</title>
<link rel="stylesheet" href="https://fonts.googleapis.com/css2?family=Open+Sans:wght@400;600;700&display=swap">
<style>
  :root {
    --backdrop: #3a3633;
    --card-black: #101010;
    --brand-orange: #f2a007;
    --text-light: #f2f2f2;
    --text-muted: #d6d6d6;
  }
  * { box-sizing: border-box; margin: 0; padding: 0; }
  html, body {
    width: 1200px;
    height: 900px;
    overflow: hidden;
    background: var(--backdrop);
    font-family: "Open Sans", Arial, sans-serif;
  }
  .sheet {
    position: relative;
    width: 1200px;
    height: 900px;
  }
  .card {
    position: absolute;
    width: 540px;
    height: 330px;
    border-radius: 3px;
    overflow: hidden;
    box-shadow: 0 10px 30px rgba(0,0,0,0.45);
  }
  .card-front {
    left: 40px;
    top: 330px;
    background: var(--card-black);
  }
  .card-back {
    left: 620px;
    top: 240px;
    background: var(--brand-orange);
    display: flex;
    align-items: center;
    justify-content: center;
  }
  .brand-name {
    color: var(--text-light);
    font-weight: 600;
    letter-spacing: 0.04em;
    line-height: 1.15;
  }
  .card-front .brand-name {
    position: absolute;
    left: 34px;
    top: 58px;
    font-size: 34px;
  }
  .card-front .brand-name small {
    display: block;
    font-size: 12.5px;
    letter-spacing: 0.12em;
    text-transform: uppercase;
    margin-top: 4px;
  }
  .card-back .brand-name {
    text-align: center;
    font-size: 56px;
  }
  .card-back .brand-name small {
    display: block;
    font-size: 17px;
    letter-spacing: 0.14em;
    text-transform: uppercase;
    margin-top: 6px;
  }
  .details {
    position: absolute;
    left: 196px;
    right: 18px;
    top: 150px;
    color: var(--text-muted);
    font-size: 12px;
    line-height: 1.55;
    white-space: nowrap;
  }
  .person-name {
    color: var(--brand-orange);
    font-weight: 700;
    font-size: 17px;
    line-height: 1.3;
  }
  .person-role { margin-bottom: 6px; }
  .contact-list {
    list-style: none;
    margin-top: 8px;
  }
  .contact-list li {
    display: flex;
    align-items: center;
    gap: 7px;
  }
  .contact-icon {
    width: 11px;
    height: 11px;
    flex: none;
    fill: var(--brand-orange);
  }
</style>
</head>
<body>
<main class="sheet">

  <section class="card card-front" aria-label="Business card front">
    <div class="brand-name">Corvane<small>Electrical &amp; Communications</small></div>

    <div class="details">
      <p class="person-name">Brent Halden</p>
      <p class="person-role">Director</p>
      <p>ABN: 71208349162</p>
      <p>Lic No: 418273D</p>
      <ul class="contact-list">
        <li>
          <svg class="contact-icon" viewBox="0 0 24 24" aria-hidden="true"><path d="M6.6 10.8a15.1 15.1 0 0 0 6.6 6.6l2.2-2.2a1 1 0 0 1 1-.25 11.4 11.4 0 0 0 3.6.57 1 1 0 0 1 1 1V20a1 1 0 0 1-1 1A17 17 0 0 1 3 4a1 1 0 0 1 1-1h3.5a1 1 0 0 1 1 1c0 1.25.2 2.45.57 3.57a1 1 0 0 1-.25 1z"/></svg>
          <span>0481209736</span>
        </li>
        <li>
          <svg class="contact-icon" viewBox="0 0 24 24" aria-hidden="true"><path d="M2 5h20v14H2z"/><path d="M3 6l9 7 9-7" fill="none" stroke="var(--card-black)" stroke-width="1.6"/></svg>
          <span>brent@corvaneelectricalandcomms.example.com.au</span>
        </li>
        <li>
          <svg class="contact-icon" viewBox="0 0 24 24" aria-hidden="true"><circle cx="12" cy="12" r="11"/><path d="M1 12h22M12 1c3.5 3.5 3.5 18.5 0 22M12 1c-3.5 3.5-3.5 18.5 0 22" fill="none" stroke="var(--card-black)" stroke-width="1.4"/></svg>
          <span>corvaneelectricalandcomms.example.com.au</span>
        </li>
      </ul>
    </div>
  </section>

  <section class="card card-back" aria-label="Business card back">
    <div class="brand-name">Corvane<small>Electrical &amp; Communications</small></div>
  </section>

</main>
</body>
</html>
```